Business card design needed

I have a leadership coaching and consultancy business which specialises in the education sector. I would like a clean, professional design). The design needs to speak to strength, support, new learning, connections & a growth mindest.

I am also looking for a unique LOGO. This is very important.

Target Market(s)

Educational Leaders & executives

Industry/Entity Type

Leadership

Contact Information for Business Card

Marnie Holbrook
Principal Coach & Consultant
Marnie Holbrook Coaching & Consulting
0491 263 814
marnie.holbrook@vendamail.example
I also would like my facebook, twitter and linkedin accounts to appear

Logo styles of interest
Lettermark Logo
Requirements
Must have
• A 2 sided business card with contact details on the back
A logo

```html
<!DOCTYPE html>
<html lang="en">
<head>
<meta charset="utf-8">
<title>Marnie Holbrook Coaching &amp; Consulting — Business Card</title>
<link rel="stylesheet" href="https://fonts.googleapis.com/css2?family=Mulish:wght@800&family=Saira+Semi+Condensed:wght@500&display=swap">
<style>
  :root {
    --teal: #0e5e5f;
    --teal-soft: #3a7e7c;
    --orange: #f3a23a;
    --ink: #141414;
    --paper: #ffffff;
  }
  * { box-sizing: border-box; margin: 0; padding: 0; }
  html, body { width: 1200px; height: 965px; overflow: hidden; background: var(--paper); }
  .canvas { position: relative; width: 1200px; height: 965px; }

  .card {
    position: absolute;
    left: 339px;
    width: 545px;
    height: 349px;
    box-shadow: 0 3px 10px rgba(0,0,0,0.35);
  }

  /* Front */
  .card--front { top: 120px; background: var(--teal); }
  .card__border {
    position: absolute; inset: 12px;
    border: 2px dashed var(--orange);
  }
  .brand-ring {
    position: absolute; left: 150px; top: 48px;
    width: 244px; height: 244px; border-radius: 50%;
    background: var(--ink);
    display: flex; align-items: center; justify-content: center;
  }
  .brand-disc {
    width: 206px; height: 206px; border-radius: 50%;
    background: var(--orange);
    display: flex; align-items: center; justify-content: center;
    text-align: center;
    font-family: "Mulish", sans-serif; font-weight: 800;
    font-size: 22px; line-height: 1.15; color: var(--ink);
    padding: 0 24px;
  }
  .ribbon { position: absolute; left: 17px; top: 283px; width: 513px; height: 38px; }
  .ribbon__label {
    position: absolute; inset: 0;
    display: flex; align-items: center; justify-content: center;
    font-family: "Mulish", sans-serif; font-weight: 800;
    font-size: 23px; color: var(--ink); white-space: nowrap;
  }

  /* Back */
  .card--back {
    top: 487px;
    background: repeating-linear-gradient(135deg,
      var(--orange) 0 31px, var(--teal) 31px 62px);
  }
  .contact-list { position: absolute; left: 70px; top: 113px; list-style: none; }
  .contact-row {
    display: flex; align-items: center;
    height: 38px; margin-bottom: 6px;
  }
  .contact-row__icon {
    width: 46px; height: 38px;
    display: flex; align-items: center; justify-content: center;
    color: var(--ink);
    font-family: "Mulish", sans-serif; font-weight: 800; font-size: 32px;
  }
  .contact-row__field {
    width: 334px; height: 38px;
    padding: 0 8px;
    background: var(--teal-soft);
    box-shadow: 0 2px 5px rgba(0,0,0,0.45);
    display: flex; align-items: center; justify-content: center;
    font-family: "Saira Semi Condensed", "Arial Narrow", sans-serif; font-weight: 500;
    font-size: 19px; line-height: 1; color: var(--ink); letter-spacing: 0.3px;
    white-space: nowrap;
  }
  .contact-row__field--email { font-size: 16px; letter-spacing: 0; }
  .icon-block { width: 26px; height: 26px; background: var(--ink); border-radius: 3px; }
  .icon-dot { width: 24px; height: 24px; background: var(--ink); border-radius: 50%; }
</style>
</head>
<body>
<main class="canvas">
  <section class="card card--front" aria-label="Card front">
    <div class="card__border"></div>
    <div class="brand-ring">
      <div class="brand-disc">Marnie Holbrook Coaching &amp; Consulting</div>
    </div>
    <div class="ribbon">
      <svg width="513" height="38" viewBox="0 0 513 38" aria-hidden="true">
        <polygon points="0,0 513,0 498,19 513,38 0,38 15,19" fill="var(--orange)"/>
      </svg>
      <p class="ribbon__label">Educational Leaders &amp; executives</p>
    </div>
  </section>

  <section class="card card--back" aria-label="Card back">
    <ul class="contact-list">
      <li class="contact-row">
        <span class="contact-row__icon"><span class="icon-dot"></span></span>
        <span class="contact-row__field">Marnie Holbrook Principal Coach</span>
      </li>
      <li class="contact-row">
        <span class="contact-row__icon"><span class="icon-block"></span></span>
        <span class="contact-row__field"></span>
      </li>
      <li class="contact-row">
        <span class="contact-row__icon"><span class="icon-block"></span></span>
        <span class="contact-row__field"></span>
      </li>
      <li class="contact-row">
        <span class="contact-row__icon">@</span>
        <span class="contact-row__field contact-row__field--email">marnie.holbrook@vendamail.example</span>
      </li>
      <li class="contact-row">
        <span class="contact-row__icon">
          <svg width="18" height="32" viewBox="0 0 18 32" aria-hidden="true">
            <rect x="0" y="4" width="18" height="28" rx="3" fill="var(--ink)"/>
            <rect x="3" y="0" width="3" height="6" fill="var(--ink)"/>
            <rect x="3" y="8" width="12" height="9" fill="var(--teal-soft)"/>
          </svg>
        </span>
        <span class="contact-row__field">0491 263 814</span>
      </li>
    </ul>
  </section>
</main>
</body>
</html>
```